Powerpoint template and intro presentation

I have a short presentation of 6 slides that I'd like to be made pretty, see attached below - called target companies Intro.

I'd also like a template incorporating my logo which I have attached below as well

I've attached a jpeg with the logo with white background that is the logo that I would like to incorporate.

Powerpoint and logo file has been uploaded

```html
<!DOCTYPE html>
<html lang="en">
<head>
<meta charset="utf-8">
<title>Smart Art 2 – Slide 13</title>
<link href="https://fonts.googleapis.com/css2?family=Didact+Gothic&display=swap" rel="stylesheet">
<style>
  :root {
    --backdrop: #ececec;
    --slide: #ffffff;
    --green: #84bd2f;
    --green-light: #b5d77f;
    --green-rule: #c8e1a8;
    --grey-rule: #c9c9c9;
    --grey-band: #dde1e4;
    --grey-text: #58595b;
    --grey-mid: #898a8d;
    --charcoal: #4a4a4e;
    --white: #ffffff;
  }
  * { margin: 0; padding: 0; box-sizing: border-box; }
  html, body { width: 1200px; height: 1000px; overflow: hidden; }
  body {
    background: var(--backdrop);
    font-family: "Didact Gothic", "Century Gothic", sans-serif;
    position: relative;
  }
  .slide {
    position: absolute; left: 33px; top: 70px;
    width: 1137px; height: 852px;
    background: var(--slide);
  }
  .brand {
    position: absolute; left: 57px; top: 78px;
    width: 150px;
    display: flex; align-items: center; gap: 10px;
    color: var(--grey-text); font-size: 17px; line-height: 1.25;
  }
  .brand-mark {
    flex: none; width: 14px; height: 14px; background: var(--green);
  }
  .slide-title {
    position: absolute; left: 229px; top: 66px;
    color: var(--green); font-size: 40px; font-weight: 400;
    letter-spacing: 2px;
  }
  .rule { position: absolute; }
  .rule--title-green { left: 229px; top: 118px; width: 906px; height: 6px; background: var(--green-rule); }
  .rule--title-grey  { left: 229px; top: 128px; width: 906px; height: 2px; background: var(--grey-rule); }
  .rule--foot-green  { left: 0; top: 792px; width: 1025px; height: 5px; background: var(--green-rule); }
  .rule--foot-grey   { left: 0; top: 802px; width: 1025px; height: 2px; background: var(--grey-rule); }
  .section-label {
    position: absolute; top: 167px; width: 502px; height: 54px;
    background: var(--grey-band); color: var(--grey-text);
    font-size: 31px; letter-spacing: 2.2px; white-space: nowrap;
    display: flex; align-items: center; justify-content: center;
  }
  .section-label--cycle { left: 57px; }
  .section-label--relationship { left: 578px; }
  .page-number {
    position: absolute; left: 1036px; top: 788px;
    width: 46px; height: 40px; border-radius: 50%;
    background: var(--green); color: var(--white);
    font-size: 17px; display: flex; align-items: center; justify-content: center;
  }
  .diagram { position: absolute; left: 0; top: 0; }
  .diagram text { font-family: "Didact Gothic", "Century Gothic", sans-serif; fill: var(--white); text-anchor: middle; }
</style>
</head>
<body>
  <div class="slide">
    <div class="brand"><span class="brand-mark"></span><span class="brand-name">Northfield Data Services</span></div>
    <h1 class="slide-title">Smart Art 2</h1>
    <div class="rule rule--title-green"></div>
    <div class="rule rule--title-grey"></div>

    <div class="section-label section-label--cycle">Smart Art Cycle in Green</div>
    <div class="section-label section-label--relationship">Smart Art Relationship in Grey</div>

    <svg class="diagram" width="1137" height="852" viewBox="33 70 1137 852">
      <g class="gear gear--large" fill="var(--charcoal)" transform="translate(399 638)">
        <circle r="96"/>
        <rect x="-13" y="-116" width="26" height="30" rx="2"/>
        <rect x="-13" y="-116" width="26" height="30" rx="2" transform="rotate(36)"/>
        <rect x="-13" y="-116" width="26" height="30" rx="2" transform="rotate(72)"/>
        <rect x="-13" y="-116" width="26" height="30" rx="2" transform="rotate(108)"/>
        <rect x="-13" y="-116" width="26" height="30" rx="2" transform="rotate(144)"/>
        <rect x="-13" y="-116" width="26" height="30" rx="2" transform="rotate(180)"/>
        <rect x="-13" y="-116" width="26" height="30" rx="2" transform="rotate(216)"/>
        <rect x="-13" y="-116" width="26" height="30" rx="2" transform="rotate(252)"/>
        <rect x="-13" y="-116" width="26" height="30" rx="2" transform="rotate(288)"/>
        <rect x="-13" y="-116" width="26" height="30" rx="2" transform="rotate(324)"/>
      </g>
      <g class="gear gear--green" fill="var(--green-light)" transform="translate(230 555)">
        <circle r="58"/>
        <rect x="-12" y="-80" width="24" height="28" rx="2"/>
        <rect x="-12" y="-80" width="24" height="28" rx="2" transform="rotate(51.4)"/>
        <rect x="-12" y="-80" width="24" height="28" rx="2" transform="rotate(102.8)"/>
        <rect x="-12" y="-80" width="24" height="28" rx="2" transform="rotate(154.2)"/>
        <rect x="-12" y="-80" width="24" height="28" rx="2" transform="rotate(205.6)"/>
        <rect x="-12" y="-80" width="24" height="28" rx="2" transform="rotate(257)"/>
        <rect x="-12" y="-80" width="24" height="28" rx="2" transform="rotate(308.4)"/>
      </g>
      <g class="gear gear--grey" fill="var(--grey-mid)" transform="translate(325 440) rotate(20)">
        <circle r="56"/>
        <rect x="-12" y="-78" width="24" height="28" rx="2"/>
        <rect x="-12" y="-78" width="24" height="28" rx="2" transform="rotate(60)"/>
        <rect x="-12" y="-78" width="24" height="28" rx="2" transform="rotate(120)"/>
        <rect x="-12" y="-78" width="24" height="28" rx="2" transform="rotate(180)"/>
        <rect x="-12" y="-78" width="24" height="28" rx="2" transform="rotate(240)"/>
        <rect x="-12" y="-78" width="24" height="28" rx="2" transform="rotate(300)"/>
      </g>
      <text x="325" y="431" font-size="18">Sample</text>
      <text x="325" y="453" font-size="18">Text</text>
      <text x="230" y="550" font-size="18">Sample</text>
      <text x="230" y="572" font-size="18">Text</text>
      <text x="399" y="646" font-size="19">Sample Text</text>

      <path d="M215 440 Q210 388 240 364" fill="none" stroke="var(--grey-mid)" stroke-width="11"/>
      <polygon points="232,355 254,351 248,374" fill="var(--grey-mid)"/>
      <path d="M190 455 Q128 478 124 544" fill="none" stroke="var(--green-light)" stroke-width="11"/>
      <polygon points="114,543 136,543 124,560" fill="var(--green-light)"/>
      <path d="M403 508 C510 506 590 630 516 722" fill="none" stroke="var(--charcoal)" stroke-width="12"/>
      <polygon points="504,716 526,730 505,742" fill="var(--charcoal)"/>

      <rect x="612" y="476" width="148" height="116" rx="9" fill="var(--charcoal)"/>
      <text x="686" y="526" font-size="34">Sample</text>
      <text x="686" y="566" font-size="34">Text</text>
      <rect x="788" y="384" width="147" height="116" rx="9" fill="var(--green-light)"/>
      <text x="862" y="434" font-size="34">Sample</text>
      <text x="862" y="474" font-size="34">Text</text>
      <rect x="963" y="476" width="148" height="116" rx="9" fill="var(--grey-mid)"/>
      <text x="1037" y="526" font-size="34">Sample</text>
      <text x="1037" y="566" font-size="34">Text</text>
      <circle cx="862" cy="657" r="78" fill="var(--green)"/>
      <text x="862" y="650" font-size="26">Sample</text>
      <text x="862" y="682" font-size="26">Text</text>

      <polygon points="849,505 875,505 875,543 886,543 862,570 838,543 849,543" fill="var(--green-light)"/>
      <polygon points="764,572 780,588 788,580 790,612 758,610 766,602 750,586" fill="var(--charcoal)"/>
      <polygon points="960,572 944,588 936,580 934,612 966,610 958,602 974,586" fill="var(--grey-mid)"/>
    </svg>

    <div class="rule rule--foot-green"></div>
    <div class="rule rule--foot-grey"></div>
    <div class="page-number">13</div>
  </div>
</body>
</html>
```